Business Card Design

We are a commercial real estate brokerage in San Francisco, leasing office buildings downtown.
I would like a clean, elegant look. Simple but powerful .

Industry/Entity Type

Business

Contact Information for Business Card

Derek Holloway
lic# 07258143
415.555.0172
derek@velt-commercial.example
velt-commercial.example

```html
<!DOCTYPE html>
<html lang="en">
<head>
<meta charset="utf-8">
<title>Velt Commercial — Business Card</title>
<link rel="stylesheet" href="https://fonts.googleapis.com/css2?family=Source+Sans+3:ital,wght@0,400;0,600;1,400&display=swap">
<style>
  :root {
    --page: #8c8d8f;
    --card: #e9eaec;
    --slate: #5d6e90;
    --ink: #454648;
    --rule: #a3a4a6;
    --charcoal: #545556;
  }
  * { box-sizing: border-box; margin: 0; padding: 0; }
  html, body { width: 1105px; height: 1200px; overflow: hidden; }
  body {
    background: var(--page);
    font-family: "Source Sans 3", "Myriad Pro", sans-serif;
    position: relative;
  }
  .card {
    position: absolute;
    left: 182px;
    width: 746px;
    height: 425px;
    background: var(--card);
    overflow: hidden;
  }
  .card--front { top: 120px; }
  .card--back { top: 637px; }

  .brand {
    position: absolute;
    right: 44px;
    top: 62px;
    display: flex;
    align-items: center;
    gap: 12px;
    color: var(--ink);
    font-size: 30px;
    font-weight: 400;
    line-height: 1;
  }
  .brand__mark {
    width: 18px;
    height: 18px;
    background: var(--slate);
  }

  .holder {
    position: absolute;
    left: 41px;
    top: 200px;
    width: 661px;
    color: var(--slate);
    font-size: 26px;
    font-weight: 600;
    letter-spacing: 0.5px;
    padding-bottom: 8px;
    border-bottom: 1.5px solid var(--rule);
  }
  .contacts {
    position: absolute;
    left: 41px;
    top: 276px;
    list-style: none;
    color: var(--ink);
    font-size: 19.5px;
  }
  .contacts li {
    display: flex;
    align-items: center;
    height: 29px;
  }
  .contacts svg { width: 17px; height: 17px; margin-right: 12px; fill: var(--ink); }
  .licence {
    position: absolute;
    right: 44px;
    top: 335px;
    color: var(--ink);
    font-size: 19.5px;
  }
  .band {
    position: absolute;
    left: 0; bottom: 0;
    width: 100%; height: 30px;
    display: flex;
  }
  .band__main { flex: 0 0 619px; background: var(--slate); }
  .band__end { flex: 1; background: var(--charcoal); }

  .back-brand {
    position: absolute;
    left: 0; right: 0;
    top: 175px;
    display: flex;
    justify-content: center;
    align-items: center;
    gap: 16px;
    color: var(--ink);
    font-size: 40px;
    font-weight: 400;
    line-height: 1;
  }
  .back-brand__mark {
    width: 24px;
    height: 24px;
    background: var(--slate);
  }
  .tagline {
    position: absolute;
    left: 0; right: 0;
    top: 316px;
    text-align: center;
    color: var(--ink);
    font-size: 19.5px;
    font-style: italic;
    line-height: 28px;
  }
</style>
</head>
<body>
  <section class="card card--front">
    <div class="brand">
      <span class="brand__mark" aria-hidden="true"></span>
      <span class="brand__name">Velt Commercial</span>
    </div>
    <h1 class="holder">DEREK HOLLOWAY</h1>
    <ul class="contacts">
      <li>
        <svg viewBox="0 0 24 24" aria-hidden="true"><path d="M6.6 10.8a15.1 15.1 0 0 0 6.6 6.6l2.2-2.2c.3-.3.7-.4 1-.2 1.1.4 2.3.6 3.6.6.6 0 1 .4 1 1V20c0 .6-.4 1-1 1A17 17 0 0 1 3 4c0-.6.4-1 1-1h3.5c.6 0 1 .4 1 1 0 1.3.2 2.5.6 3.6.1.3 0 .7-.2 1z"/></svg>
        415.555.0172
      </li>
      <li>
        <svg viewBox="0 0 24 24" aria-hidden="true"><path d="M2 5h20v14H2zm2 2v.5l8 5 8-5V7zm0 2.8V17h16V9.8l-8 5z"/></svg>
        derek@velt-commercial.example
      </li>
      <li>
        <svg viewBox="0 0 24 24" aria-hidden="true"><path d="M12 2a10 10 0 1 0 0 20 10 10 0 0 0 0-20zm-1 17.9A8 8 0 0 1 4.1 10L9 15v1a2 2 0 0 0 2 2zm6.9-2.5A2 2 0 0 0 16 16h-1v-3a1 1 0 0 0-1-1H8v-2h2a1 1 0 0 0 1-1V7h2a2 2 0 0 0 2-2v-.4a8 8 0 0 1 2.9 12.8z"/></svg>
        velt-commercial.example
      </li>
    </ul>
    <p class="licence">lic# 07258143</p>
    <div class="band"><span class="band__main"></span><span class="band__end"></span></div>
  </section>

  <section class="card card--back">
    <div class="back-brand">
      <span class="back-brand__mark" aria-hidden="true"></span>
      <span class="back-brand__name">Velt Commercial</span>
    </div>
    <p class="tagline">commercial real estate brokerage in San Francisco<br>leasing office buildings downtown.</p>
  </section>
</body>
</html>
```